Business Card Design

We custom build & and install Air filtration systems for mining machines - the system filters the air going into the cabin to protect the operator/driver Examples of the machines we install our units to would be Ironhaven or Veltoro. Australian owned company Our company colors are sky blue with polished Stainless steel lettering & framing. I have a logo which I will upload but I would like the new image to be crisper.

Industry/Entity Type

Business

Contact Information for Business Card

Company name - Clearlung Pty Ltd
Dale Morrissey - Position - Sales & Product Development Contact numbers Mob 0428 359 162 Tel - 07 3581 4296
Address - 147 Quarrel Rd, Wendlebury, Brisbane 4108, Australia

Colors
0255a3

Requirements
Must have
• sky blue & polished chrome lettering

```html
<!DOCTYPE html>
<html lang="en">
<head>
<meta charset="utf-8">
<title>Clearlung – Business Card</title>
<link rel="stylesheet" href="https://fonts.googleapis.com/css2?family=Exo+2:wght@400;600;800&display=swap">
<style>
  :root {
    --page-bg: #e9ebef;
    --card-white: #ffffff;
    --card-silver: #d9dce1;
    --brand-blue: #26479a;
    --brand-lilac: #6a70b8;
    --accent-cyan: #1aa9e0;
    --ink-dark: #2e2f33;
    --text-light: #ffffff;
  }
  * { margin: 0; padding: 0; box-sizing: border-box; }
  html, body {
    width: 1200px; height: 900px; overflow: hidden;
    background: var(--page-bg);
    font-family: "Exo 2", sans-serif;
  }
  .card {
    position: absolute; left: 100px; top: 170px;
    width: 1000px; height: 560px;
    border-radius: 44px; overflow: hidden;
    background: linear-gradient(160deg, var(--card-silver) 0%, var(--card-white) 45%);
    box-shadow: 0 18px 40px rgba(20, 30, 60, 0.25);
  }
  .card-waves { position: absolute; inset: 0; width: 100%; height: 100%; }
  .brand-name {
    position: absolute; left: 70px; top: 62px;
    font-weight: 800; font-size: 66px; letter-spacing: 1px;
    color: var(--brand-blue); line-height: 1;
  }
  .person { position: absolute; left: 200px; top: 300px; text-align: center; width: 340px; }
  .person-name {
    font-weight: 600; font-size: 27px; letter-spacing: 1.5px;
    color: var(--ink-dark); text-transform: uppercase;
  }
  .person-role { font-size: 19px; color: var(--accent-cyan); margin-top: 2px; }
  .contact-list {
    position: absolute; right: 56px; top: 190px;
    list-style: none; text-align: right;
    color: var(--text-light); font-size: 18px; letter-spacing: 1px;
  }
  .contact-list li {
    display: flex; justify-content: flex-end; align-items: center;
    gap: 10px; height: 40px;
  }
  .contact-icon { width: 20px; height: 20px; fill: var(--text-light); flex: none; }
  .address {
    position: absolute; left: 70px; top: 448px;
    font-style: normal;
    color: var(--text-light); font-size: 22px; letter-spacing: 1.2px; line-height: 1.45;
  }
</style>
</head>
<body>
  <div class="card">
    <svg class="card-waves" viewBox="0 0 1000 560" preserveAspectRatio="none" aria-hidden="true">
      <path d="M0,334 C170,406 330,436 470,406 C600,376 640,206 740,136 C820,86 900,76 1000,66 L1000,560 L0,560 Z" fill="var(--brand-lilac)"/>
      <path d="M0,352 C170,424 330,454 470,424 C600,394 640,224 740,154 C820,104 900,94 1000,84 L1000,560 L0,560 Z" fill="var(--card-white)"/>
      <path d="M0,368 C170,440 330,470 470,440 C600,410 640,240 740,170 C820,120 900,110 1000,100 L1000,560 L0,560 Z" fill="var(--brand-blue)"/>
    </svg>

    <div class="brand-name">Clearlung</div>

    <div class="person">
      <p class="person-name">Dale Morrissey</p>
      <p class="person-role">Sales &amp; Product Development</p>
    </div>

    <ul class="contact-list">
      <li>07 3581 4296
        <svg class="contact-icon" viewBox="0 0 24 24"><path d="M6.6 10.8a15.1 15.1 0 0 0 6.6 6.6l2.2-2.2a1 1 0 0 1 1-.25 11.4 11.4 0 0 0 3.6.57 1 1 0 0 1 1 1V20a1 1 0 0 1-1 1A17 17 0 0 1 3 4a1 1 0 0 1 1-1h3.5a1 1 0 0 1 1 1c0 1.25.2 2.45.57 3.6a1 1 0 0 1-.25 1z"/></svg>
      </li>
      <li>0428 359 162
        <svg class="contact-icon" viewBox="0 0 24 24"><path d="M7 1h10a2 2 0 0 1 2 2v18a2 2 0 0 1-2 2H7a2 2 0 0 1-2-2V3a2 2 0 0 1 2-2zm0 3v14h10V4zm5 15.5a1.2 1.2 0 1 0 0 2.4 1.2 1.2 0 0 0 0-2.4z"/></svg>
      </li>
      <li>07 3581 4297
        <svg class="contact-icon" viewBox="0 0 24 24"><path d="M6 2h9l3 3v5H6zM3 11h18a1 1 0 0 1 1 1v8a1 1 0 0 1-1 1H3a1 1 0 0 1-1-1v-8a1 1 0 0 1 1-1zm3 3v2h3v-2zm5 0v2h3v-2zm5 0v2h3v-2z"/></svg>
      </li>
      <li>dale@clearlungfilters.com.au
        <svg class="contact-icon" viewBox="0 0 24 24"><path d="M2 5h20v14H2zm2 2v.5l8 5.5 8-5.5V7zm0 2.9V17h16V9.9l-8 5.5z"/></svg>
      </li>
      <li>www.clearlungfilters.com.au
        <svg class="contact-icon" viewBox="0 0 24 24"><path d="M12 2a10 10 0 1 0 0 20 10 10 0 0 0 0-20zm6.9 9h-3a15 15 0 0 0-1.3-5.6A8 8 0 0 1 18.9 11zM12 4.1c.9 1.2 1.7 3.6 1.9 6.9h-3.8c.2-3.3 1-5.7 1.9-6.9zM9.4 5.4A15 15 0 0 0 8.1 11h-3a8 8 0 0 1 4.3-5.6zM5.1 13h3a15 15 0 0 0 1.3 5.6A8 8 0 0 1 5.1 13zm6.9 6.9c-.9-1.2-1.7-3.6-1.9-6.9h3.8c-.2 3.3-1 5.7-1.9 6.9zm2.6-1.3a15 15 0 0 0 1.3-5.6h3a8 8 0 0 1-4.3 5.6z"/></svg>
      </li>
    </ul>

    <address class="address">147 Quarrel Rd, Wendlebury<br>Brisbane 4108, Australia</address>
  </div>
</body>
</html>
```